Property management company looking for modern card design

We at Blue Heron Partners provides property management services for its residential and commercial properties, with expertise in all categories of multifamily, industrial and office projects throughout California.

We need a business card design that is professional and modern designed business card. In our field, clients get hundreds of business cards, we would like our card to stand out.

Please avoid small print.

Target Market(s)

Professionals and high end clients

Industry/Entity Type

Financial Planning

Contact Information for Business Card

Company Name: Blue Heron Partners, Name, email, license #, phone number, website blueheronpartners.com

Font styles to use
Sans Serif

Requirements
Must have
• The card design needs to be adaptable because there is a possibly we will be expanding into different sectors other than real estate. The card design should be focused on financial planning and asset management.
Nice to have
• Modern and simple business card. Eye catching. Non-standard size/shaped cards would be great.
• blueheronpartners.com
Should not have
• Too many bright color or any pictures or shapes of real estate stuff.

```html
<!DOCTYPE html>
<html lang="en">
<head>
<meta charset="utf-8">
<title>Blue Heron Partners – Business Card</title>
<link rel="stylesheet" href="https://fonts.googleapis.com/css2?family=Open+Sans:wght@400;600&family=Roboto:wght@400&display=swap">
<style>
  :root {
    --stage-top: #2a2a2a;
    --stage-bottom: #050505;
    --card-white: #ffffff;
    --brand-red: #d81e2c;
    --brand-deep: #7d0d16;
    --ink-dark: #6a0a12;
    --panel-dark: #8c0f18;
    --panel-mid: #c21c28;
    --panel-glow: #f27a83;
    --on-red: #ffffff;
  }
  * { margin: 0; padding: 0; box-sizing: border-box; }
  html, body { width: 1200px; height: 900px; overflow: hidden; }
  body {
    background: radial-gradient(ellipse at 50% 20%, var(--stage-top) 0%, #141414 55%, var(--stage-bottom) 100%);
    position: relative;
    font-family: "Open Sans", sans-serif;
  }
  .card {
    position: absolute;
    top: 184px;
    height: 490px;
    border-radius: 14px;
    overflow: hidden;
  }
  .card-front {
    left: 299px;
    width: 301px;
    background: var(--card-white);
    text-align: center;
  }
  .brand-dot {
    position: absolute;
    left: 103px;
    top: 71px;
    width: 94px;
    height: 94px;
    border-radius: 50%;
    background: radial-gradient(circle at 50% 50%, var(--panel-mid) 0%, var(--brand-deep) 100%);
  }
  .brand-name {
    position: absolute;
    left: 0; right: 0;
    top: 170px;
    font-family: "Roboto", sans-serif;
    font-weight: 400;
    font-size: 52px;
    letter-spacing: -1.5px;
    color: var(--brand-red);
    line-height: 1.1;
  }
  .person-name {
    position: absolute; left: 0; right: 0; top: 277px;
    font-weight: 600; font-size: 16px; color: var(--brand-red);
  }
  .person-title {
    position: absolute; left: 0; right: 0; top: 297px;
    font-size: 13px; color: var(--ink-dark);
  }
  .license {
    position: absolute; left: 0; right: 0; top: 339px;
    font-size: 13px; color: var(--ink-dark);
  }
  .license strong { font-weight: 600; font-size: 14px; color: var(--brand-red); }
  .contact {
    position: absolute; left: 0; right: 0; top: 369px;
    list-style: none;
    font-size: 13px; line-height: 18px; color: var(--ink-dark);
  }
  .card-back {
    left: 645px;
    width: 305px;
    background: linear-gradient(160deg, var(--panel-dark) 0%, var(--panel-mid) 50%, var(--panel-dark) 100%);
  }
  .back-glow {
    position: absolute;
    left: 0; top: 0;
    width: 305px; height: 490px;
  }
  .back-name {
    position: absolute; left: 0; right: 0; top: 336px;
    text-align: center;
    font-family: "Roboto", sans-serif;
    font-weight: 400;
    color: var(--on-red);
  }
  .back-name .line-main {
    display: block; font-size: 52px; letter-spacing: -1.5px; line-height: 64px;
  }
  .back-name .line-sub {
    display: block; font-size: 26px; letter-spacing: 1px; line-height: 30px;
  }
</style>
</head>
<body>
  <section class="card card-front">
    <div class="brand-dot"></div>
    <div class="brand-name">Blue Heron</div>
    <p class="person-name">Daniel Hartley</p>
    <p class="person-title">Managing Director</p>
    <p class="license"><strong>License:</strong> BHP01245</p>
    <ul class="contact">
      <li>044-987 650 312</li>
      <li>info@blueheronpartners.com</li>
      <li>www.blueheronpartners.com</li>
    </ul>
  </section>

  <section class="card card-back">
    <svg class="back-glow" viewBox="0 0 305 490" role="img" aria-label="Soft red radial glow where the brand pattern sits">
      <defs>
        <radialGradient id="backGlow" cx="155" cy="245" r="200" gradientUnits="userSpaceOnUse">
          <stop offset="0" stop-color="var(--panel-glow)" style="stop-color:#f27a83"/>
          <stop offset="0.35" stop-color="#d8303c"/>
          <stop offset="1" stop-color="#d8303c" stop-opacity="0"/>
        </radialGradient>
      </defs>
      <rect width="305" height="490" fill="url(#backGlow)"/>
    </svg>
    <div class="back-name">
      <span class="line-main">Blue Heron</span>
      <span class="line-sub">PARTNERS</span>
    </div>
  </section>
</body>
</html>
```